Tidewell Climate Business Card Design

Design new, 2 sides, business cards for a residential and light commercial heating, air conditioning contractor.

Target Market(s)

Homeowners, small businesses

Industry/Entity Type

Business

Contact Information for Business Card

Dominic Westerhall
Phone - 862-415-2736
Email
Address - PO box 518
Brightwater NJ 07912
Website - www.TidewellClimateLLC.example

Requirements
Must have
• logo, company colors, standard size with no die cut, so I can use nova stamp

```html
<!DOCTYPE html>
<html lang="en">
<head>
<meta charset="utf-8">
<title>Tidewell Climate Business Card</title>
<link rel="stylesheet" href="https://fonts.googleapis.com/css2?family=Libre+Baskerville:ital,wght@0,400;0,700;1,400&family=Arimo:wght@400;700&display=swap">
<style>
  :root {
    --backdrop: #e6e3de;
    --card-white: #ffffff;
    --card-black: #1e1e1e;
    --ink: #2a2a2a;
    --ink-soft: #4a4a4a;
    --rule: #9a9a9a;
    --reverse: #f2f2f2;
  }
  * { box-sizing: border-box; margin: 0; padding: 0; }
  html, body { width: 1200px; height: 950px; overflow: hidden; }
  body {
    background: var(--backdrop);
    display: flex;
    align-items: center;
    justify-content: center;
    gap: 90px;
    font-family: "Arimo", Arial, sans-serif;
  }
  .card {
    width: 400px;
    height: 700px;
    border-radius: 26px;
    position: relative;
    overflow: hidden;
    box-shadow: 0 6px 20px rgba(0,0,0,.18);
  }
  .card-front { background: var(--card-white); color: var(--ink); }
  .card-back { background: var(--card-black); color: var(--reverse); }

  .front-details {
    padding: 72px 30px 0;
    text-align: center;
  }
  .person-name {
    font-family: "Libre Baskerville", Georgia, serif;
    font-size: 28px;
    font-weight: 400;
    letter-spacing: .3px;
    white-space: nowrap;
  }
  .person-title {
    font-family: "Libre Baskerville", Georgia, serif;
    font-style: italic;
    font-size: 18px;
    margin-top: 8px;
    color: var(--ink-soft);
  }
  .divider { display: block; margin: 20px auto; }
  .contact-lines {
    font-size: 16px;
    line-height: 1.45;
    color: var(--ink-soft);
    white-space: nowrap;
  }
  .contact-lines b { color: var(--ink); }
  .website {
    font-size: 15px;
    font-weight: 700;
    letter-spacing: .5px;
    text-transform: uppercase;
    white-space: nowrap;
  }

  .brand-band {
    position: absolute;
    left: 0; right: 0; bottom: 0;
    height: 200px;
    background: var(--card-black);
    display: flex;
    align-items: center;
    justify-content: center;
    gap: 12px;
  }
  .brand-mark {
    width: 14px; height: 14px;
    border-radius: 50%;
    background: var(--reverse);
    flex: none;
  }
  .brand-name {
    font-family: "Libre Baskerville", Georgia, serif;
    font-weight: 700;
    font-size: 29px;
    color: var(--reverse);
    letter-spacing: .5px;
    white-space: nowrap;
  }

  .service-line {
    position: absolute;
    top: 40px;
    left: 200px;
    transform-origin: left top;
    transform: rotate(90deg) translateY(-50%);
    width: 420px;
    font-family: "Libre Baskerville", Georgia, serif;
    font-style: italic;
    font-size: 16px;
    line-height: 1.6;
    text-align: center;
    color: var(--reverse);
  }
</style>
</head>
<body>
  <section class="card card-front" aria-label="Business card front">
    <div class="front-details">
      <h1 class="person-name">Dominic Westerhall</h1>
      <p class="person-title">CEO/Founder</p>
      <svg class="divider" width="260" height="12" viewBox="0 0 260 12" aria-hidden="true">
        <line x1="0" y1="6" x2="120" y2="6" stroke="var(--rule)" stroke-width="1"/>
        <rect x="125" y="1" width="10" height="10" transform="rotate(45 130 6)" fill="var(--ink)"/>
        <line x1="140" y1="6" x2="260" y2="6" stroke="var(--rule)" stroke-width="1"/>
      </svg>
      <div class="contact-lines">
        <p>PO box 518</p>
        <p>Brightwater NJ 07912</p>
        <p><b>P.</b> 862-415-2736 <b>M.</b> 862-415-9017</p>
        <p><b>E.</b> dominic@tidewellclimate.example</p>
      </div>
      <svg class="divider" width="260" height="12" viewBox="0 0 260 12" aria-hidden="true">
        <line x1="0" y1="6" x2="120" y2="6" stroke="var(--rule)" stroke-width="1"/>
        <rect x="125" y="1" width="10" height="10" transform="rotate(45 130 6)" fill="var(--ink)"/>
        <line x1="140" y1="6" x2="260" y2="6" stroke="var(--rule)" stroke-width="1"/>
      </svg>
      <p class="website">www.TidewellClimateLLC.example</p>
    </div>
    <div class="brand-band">
      <span class="brand-mark"></span>
      <span class="brand-name">Tidewell Climate</span>
    </div>
  </section>

  <section class="card card-back" aria-label="Business card back">
    <p class="service-line">Residential &amp; light commercial heating<br>Air conditioning contractor</p>
    <div class="brand-band">
      <span class="brand-mark"></span>
      <span class="brand-name">Tidewell Climate</span>
    </div>
  </section>
</body>
</html>
```